Annual review for The Harrow Collective

The Harrow Collective is a small public relations agency in London specialising in corporate and public affairs. Most of our work is international and we have a strong connection to South Africa. We would like to prepare a short annual review for 2016. The review will serve as both a review of our activities in 2016, and as a credentials document. Content then will include:
1. An introduction to the business
2. Who we are
3. Projects and clients undertaken in 2016
4. News and views
We imagine it will be used mostly as a pdf but would like it to be suitable for print. We envisage it to be about 8 pages long. The design look and feel should convey a business, while small, of stature. We shall include some of our client logos but we would welcome the use of some photography / imagery to have visual impact (although we don't have very much of our own!). The corporate look and feel is white, grey and black.

Industry/Entity Type

Public Relation

Font styles to use
Sans Serif

Requirements
Must have
• My project must convey a business with flair and gravitas, that punches above its weight.
Nice to have
• Thoughtful use of imagery.

```html
<!DOCTYPE html>
<html lang="en">
<head>
<meta charset="utf-8">
<title>The Harrow Collective — Annual Review 2016 Cover</title>
<link rel="stylesheet" href="https://fonts.googleapis.com/css2?family=Open+Sans:wght@300;400;600;700&display=swap">
<style>
  :root {
    --backdrop: #d6d6d6;
    --paper: #ffffff;
    --ink: #58595b;
    --band: #6a6b6e;
    --band-text: #f2f2f2;
    --photo-light: #a9a9a9;
    --photo-mid: #6f6f6f;
    --photo-dark: #3a3a3a;
  }
  * { margin: 0; padding: 0; box-sizing: border-box; }
  html, body {
    width: 1200px; height: 960px; overflow: hidden;
    background: var(--backdrop);
    font-family: "Open Sans", Arial, sans-serif;
  }
  .spread {
    position: absolute; left: 40px; top: 84px;
    width: 1120px; height: 792px;
    display: flex; background: var(--paper);
  }
  .page { position: relative; width: 560px; height: 100%; }
  .page--back {
    background: linear-gradient(to right, var(--paper) 88%, #f1f1f1 100%);
  }
  .brand {
    position: absolute; left: 0; right: 0;
    display: flex; align-items: center; justify-content: center; gap: 12px;
    color: var(--ink); font-weight: 600; font-size: 22px; letter-spacing: 0.2px;
  }
  .brand__dot {
    width: 24px; height: 24px; border: 2px solid var(--ink); border-radius: 50%;
  }
  .page--back .brand { top: 119px; }
  .contact-band {
    position: absolute; left: 0; top: 287px; width: 100%; height: 246px;
    background: var(--band); color: var(--band-text);
    text-align: center; font-size: 11px; line-height: 17px;
    padding-top: 50px; text-transform: uppercase;
  }
  .contact-band address { font-style: normal; margin-bottom: 17px; }
  .contact-band .email { text-transform: none; }
  .website {
    position: absolute; left: 0; right: 0; top: 637px;
    text-align: center; color: var(--ink);
    font-weight: 300; font-size: 14px; letter-spacing: 2.6px;
  }
  .cover-photo {
    position: absolute; left: 0; top: 0; width: 100%; height: 533px;
    background:
      linear-gradient(to bottom, rgba(0,0,0,0) 0 287px, rgba(20,20,20,0.35) 287px 533px),
      linear-gradient(160deg, #dcdcdc 0%, var(--photo-light) 12%, var(--photo-mid) 30%, var(--photo-dark) 50%, var(--photo-mid) 62%, var(--photo-light) 75%, var(--photo-dark) 100%);
  }
  .cover-title {
    position: absolute; left: 0; right: 0; top: 400px;
    text-align: center; color: #ffffff;
    font-weight: 700; font-size: 14px; letter-spacing: 5px;
  }
  .page--front .brand { top: 640px; }
</style>
</head>
<body>
  <main class="spread">
    <section class="page page--back">
      <div class="brand"><span class="brand__dot"></span>The Harrow Collective</div>
      <div class="contact-band">
        <address>The Harrow Collective<br>12. Rue des Lilas<br>75011 Paris</address>
        <address>The Harrow Collective<br>41 Marlow Street<br>London W1A 2XY</address>
        <p class="email">E: info@harrowcollective.com</p>
      </div>
      <p class="website">www.theharrowcollective.com</p>
    </section>
    <section class="page page--front">
      <div class="cover-photo" role="img" aria-label="Black and white aerial photograph of a rocky cape with cliffs, a sandy beach and the ocean under a cloudy sky"></div>
      <h1 class="cover-title">ANNUAL REVIEW &nbsp;|&nbsp; 2016</h1>
      <div class="brand"><span class="brand__dot"></span>The Harrow Collective</div>
    </section>
  </main>
</body>
</html>
```